Creation of a Velmaro website

Velmaro is a company% 26 # 233; t% 26 # 233; consulting that accompanies Swiss companies or% 26 # 233; strang% 26 # 232; res in the d% 26 # 233; development of their business on the market% 26 # 233; Switzerland by providing strategic contacts (personalized contact program% 26 # 233; s) or market information% 26 # 233; (% 26 # 233; market research% 26 # 233;) and by providing administrative support (repr% 26 # 233; tax representation) or logistics (organization of% 26 # 233; v% 26 # 233; nement, assistance for participation% 26 # 224; fairs). Our customers are mainly European companies wishing to develop their business in Switzerland. N% 26 # 233; however, our services are% 26 # 233; also aimed at Swiss companies wishing to develop in other parts of Switzerland. Our site must therefore be% 26 # 234; capable of being translated into several languages. The services offered% 26 # 233; s by Velmaro may also% 26 # 233; also% 26 # 39;% 26 # 233; tender% 26 # 224; promoting tourism in Switzerland for countries or regions% 26 # 233; foreigners or% 26 # 224; the promotion of trade fairs or fairs with% 26 # 232; sd% 26 # 39; companies of the sectors concerned% 26 # 233; s. It is therefore n% 26 # 233; necessary to be able to add sub-headings of services which can% 26 # 234; be displayed% 26 # 233; es or hide% 26 # 233; es as required. We are 2 associates% 26 # 233; s, low% 26 # 233; s in the French-speaking parts (Neuch% 26 # 226; tel) and al% 26 # 233; manique (Zurich) of Switzerland.

Target Market(s)

Swiss or European companies wishing to develop their activities in Switzerland.

Coding

Coded - Design and coding required

Colors

Designer to choose colors to be used in the design.

Requirements
Must have
• A home page A section of% 26 # 233; writing the services offered% 26 # 233; es by Velmaro with the possibility% 26 # 233; d% 26 # 39; add sub-headings which can% 26 # 234; be displayed% 26 # 233; e or hidden% 26 # 233; e A page with the r% 26 # 233; f% 26 # 233; which can be displayed% 26 # 233; e or hidden% 26 # 233; e A page of% 26 # 233; writing l% 26 # 39;% 26 # 233; team A page with form contact, addresses and int card% 26 # 233; gr% 26 # 233; e The site must% 26 # 234; be low% 26 # 233; on a CMS allowing% 26 # 39;% 26 # 234; to be autonomous in modifying the website The possibility% 26 # 233; to be able to translate the site into several languages (FR, EN, DE, IT, NL, ...)

```html
<!DOCTYPE html>
<html lang="en">
<head>
<meta charset="utf-8">
<title>Velmaro — Market Research and Logistics</title>
<link href="https://fonts.googleapis.com/css2?family=Montserrat:wght@400;500;600;700;800&family=Lato:wght@400;700&display=swap" rel="stylesheet">
<style>
:root{
  --navy:#1b3249;
  --navy-deep:#142638;
  --steel:#95a5ba;
  --steel-light:#d7dde5;
  --ink:#1f3348;
  --text:#3c4756;
  --muted:#6b7684;
  --white:#ffffff;
}
*{margin:0;padding:0;box-sizing:border-box}
html,body{width:1200px;height:3702px;overflow:hidden}
body{position:relative;background:var(--white);font-family:"Lato",sans-serif;color:var(--text)}
.abs{position:absolute}
.head{font-family:"Montserrat",sans-serif}

/* nav */
.topbar{left:0;top:0;width:1200px;height:90px;background:var(--white)}
.brand{left:100px;top:24px;display:flex;align-items:center;gap:16px}
.brand-mark{width:44px;height:44px;border-radius:10px;background:var(--navy)}
.brand-name{font-family:"Montserrat",sans-serif;font-size:34px;font-weight:500;letter-spacing:3px;color:var(--navy)}
.nav{left:488px;top:36px;display:flex;gap:0;font-family:"Montserrat",sans-serif;font-size:14px;font-weight:500;color:#4c6580}
.nav span{position:absolute;white-space:nowrap}
.nav .active{color:var(--navy);font-weight:700}
.nav .active::after{content:"";position:absolute;left:0;right:0;top:24px;height:3px;background:var(--navy)}

/* hero */
.hero{left:0;top:90px;width:1200px;height:672px}
.hero-copy{left:0;top:300px;width:1200px;text-align:center;color:var(--white);font-family:"Montserrat",sans-serif}
.hero-welcome{font-size:29px;font-weight:400;letter-spacing:1px}
.hero-title{font-size:58px;font-weight:800;line-height:62px;margin-top:14px}
.hero-sub{font-size:58px;font-weight:400;line-height:62px}

/* about */
.about-photo{left:168px;top:818px;width:375px;height:377px;border-radius:110px;background:linear-gradient(135deg,#8a7a66,#5b5048 55%,#3a3a3c)}
.about-title{left:594px;top:843px;font-size:34px;font-weight:700;color:var(--ink)}
.about-text{left:596px;top:910px;width:500px;font-size:18px;line-height:25px;color:var(--text)}
.about-text p+p{margin-top:28px}
.btn-dark{left:598px;top:1121px;width:182px;height:52px;background:var(--navy);color:var(--white);border-radius:0 26px 0 26px;font-family:"Montserrat",sans-serif;font-size:16px;font-weight:500;display:flex;align-items:center;justify-content:center}

/* services */
.services{left:0;top:1275px;width:1200px;height:552px;background:linear-gradient(120deg,#e9ecf0,#d5dbe2 45%,#e4e7eb)}
.section-title{font-family:"Montserrat",sans-serif;font-weight:700;font-size:30px;text-align:center;width:1200px;left:0}
.svc{position:absolute;display:flex;flex-direction:column;align-items:center;text-align:center;color:var(--white)}
.svc-diamond{position:absolute;border-radius:70px;transform:rotate(45deg)}
.svc-body{position:relative;width:220px;display:flex;flex-direction:column;align-items:center}
.svc-name{font-family:"Montserrat",sans-serif;font-size:18px;font-weight:600;margin-top:10px}
.svc-desc{font-size:13px;line-height:19px;margin-top:8px;opacity:.85}

/* team */
.team{left:0;top:1827px;width:1200px;height:493px;background:var(--navy)}
.team-sub{left:0;top:1908px;width:1200px;text-align:center;color:var(--white);font-size:13px}
.member{position:absolute;top:1972px;width:200px;text-align:center;color:var(--white)}
.member-photo{width:163px;height:163px;border-radius:50%;margin:0 auto;background:radial-gradient(circle at 50% 40%,#a6907c,#5a4c44 70%)}
.member-name{font-family:"Montserrat",sans-serif;font-size:14px;font-weight:600;letter-spacing:1px;margin-top:20px}
.member-desc{font-size:12px;line-height:17px;margin-top:10px;opacity:.85}
.member-btn{width:102px;height:36px;border:1.5px solid var(--white);margin:15px auto 0;font-family:"Montserrat",sans-serif;font-size:13px;font-weight:600;display:flex;align-items:center;justify-content:center}

/* projects */
.projects-sub{left:200px;top:2420px;width:800px;text-align:center;font-size:12px;line-height:15px;color:var(--text);font-family:Arial,sans-serif}
.card{position:absolute;top:2492px;width:278px;height:393px;background:var(--white);box-shadow:0 1px 5px rgba(0,0,0,.2)}
.card-photo{height:172px}
.card-body{padding:26px 27px 0 27px}
.card-tag{font-size:10px;font-weight:700;color:var(--navy);font-family:Arial,sans-serif}
.card-title{font-size:16px;line-height:20px;color:#222;margin-top:16px;font-family:Arial,sans-serif}
.card-text{font-size:9.5px;line-height:14px;color:#555;text-align:justify;text-align-last:center;margin-top:12px;font-family:Arial,sans-serif}
.dots{left:570px;top:2920px;display:flex;gap:7px;align-items:center}
.dot{width:6px;height:6px;border-radius:50%;background:var(--navy)}
.dot.on{width:11px;height:11px;background:none;border:2px solid var(--navy)}

/* contact */
.contact{left:0;top:2983px;width:1200px;height:719px;background:linear-gradient(180deg,#23384e,#1a2d41 60%,#1c3047)}
.contact-title{left:163px;top:3088px;font-size:30px;font-weight:700;color:var(--white)}
.info{position:absolute;left:165px;display:flex;gap:22px;color:var(--white)}
.info-label{font-family:"Montserrat",sans-serif;font-size:17px;font-weight:600}
.info-value{font-size:18px;margin-top:4px}
.field{position:absolute;left:621px;width:466px;border:1.5px solid #8595a8;color:var(--white);font-family:"Montserrat",sans-serif;font-size:15px;padding:11px 21px}
.btn-light{left:626px;top:3355px;width:181px;height:50px;background:var(--steel);color:var(--navy);border-radius:0 25px 0 25px;font-family:"Montserrat",sans-serif;font-size:16px;font-weight:600;display:flex;align-items:center;justify-content:center}
.foot-links{top:3564px;font-family:"Montserrat",sans-serif;font-size:16px;font-weight:600;color:var(--navy)}
.foot-links span{position:absolute;white-space:nowrap}
.copy{left:0;top:3598px;width:1200px;text-align:center;font-size:13px;color:#555}
.social{top:3632px;width:36px;height:36px;border-radius:50%;background:var(--navy)}
</style>
</head>
<body>

<header class="abs topbar">
  <div class="abs brand"><div class="brand-mark"></div><div class="brand-name">VELMARO</div></div>
  <nav class="abs nav">
    <span class="active" style="left:0">HOME</span>
    <span style="left:83px">ABOUT US</span>
    <span style="left:196px">OUR SERVICES</span>
    <span style="left:336px">TEAM</span>
    <span style="left:417px">CONTACT</span>
    <span style="left:526px;color:var(--navy);font-weight:700">EN &#8964;</span>
  </nav>
</header>

<section class="abs hero">
  <svg width="1200" height="672" viewBox="0 0 1200 672" style="position:absolute;left:0;top:0">
    <defs>
      <linearGradient id="heroFill" x1="0" y1="0" x2="0" y2="1">
        <stop offset="0" stop-color="#3d5670"/>
        <stop offset=".5" stop-color="#4e6781"/>
        <stop offset="1" stop-color="#2c4259"/>
      </linearGradient>
    </defs>
    <path role="img" aria-label="Snowy mountain range above an alpine lake, tinted blue" d="M0 0H1200V564L660 665Q600 680 540 665L0 564Z" fill="url(#heroFill)"/>
    <path d="M92 260L72 285L92 310M1108 260L1128 285L1108 310" fill="none" stroke="#fff" stroke-width="2"/>
  </svg>
  <div class="abs hero-copy" style="top:210px">
    <div class="hero-welcome">WELCOME TO VELMARO</div>
    <div class="hero-title">MARKET RESEARCH</div>
    <div class="hero-sub">AND LOGISTICS</div>
  </div>
</section>

<section>
  <div class="abs about-photo" role="img" aria-label="Desk with laptop, charts and sticky notes seen from above"></div>
  <h2 class="abs head about-title">ABOUT VELMARO</h2>
  <div class="abs about-text">
    <p>Pellentesque faucibus Ut accumsan ultricies elit Maecenas at justo id velit placerat molestie Donec dictum lectus non odio Cras a ante vitae enim iaculis aliquam</p>
    <p>Mauris nunc quam venenatis nec euismod sit amet egestas placerat est Pellentesque habitant morbi tristique senectus et netus et malesuada fames ac turpis egestas Cras id elit</p>
  </div>
  <div class="abs btn-dark">LEARN MORE</div>
</section>

<section class="abs services" role="img" aria-label="Soft blurred photo of colleagues in a meeting"></section>
<h2 class="abs section-title" style="top:1337px;color:var(--ink)">OUR SERVICES</h2>

<div class="svc" style="left:149px;top:1458px;width:220px;height:220px">
  <div class="svc-diamond" style="left:0;top:0;width:220px;height:220px;background:var(--steel)"></div>
  <div class="svc-body" style="top:32px">
    <svg width="60" height="56" viewBox="0 0 60 56" fill="none" stroke="#fff" stroke-width="1.8"><circle cx="30" cy="28" r="22"/><circle cx="30" cy="28" r="14"/><path d="M22 36V30M27 36V26M32 36V22M37 36V28"/></svg>
    <div class="svc-name">MARKET RESEARCH</div>
    <div class="svc-desc">Suspendisse quam leo molestie sed luctus quis feugiat in</div>
    <svg width="30" height="30" viewBox="0 0 30 30" fill="none" stroke="#fff" stroke-width="2.5" style="margin-top:20px"><path d="M15 3V27M5 17L15 27L25 17"/></svg>
  </div>
</div>

<div class="svc" style="left:473px;top:1440px;width:256px;height:256px">
  <div class="svc-diamond" style="left:0;top:0;width:256px;height:256px;background:var(--navy)"></div>
  <div class="svc-body" style="top:18px;width:256px">
    <svg width="70" height="62" viewBox="0 0 70 62" fill="none" stroke="#fff" stroke-width="1.8"><path d="M35 20L47 27V40L35 47L23 40V27Z M23 27L35 34L47 27M35 34V47"/><path d="M35 3V13M35 50V60M8 32H18M52 32H62M14 10L21 17M56 10L49 17M14 54L21 47M56 54L49 47"/></svg>
    <div class="svc-name">LOGISTICS</div>
    <div class="svc-desc" style="width:250px">Allamcorper est eget tempor cursus neque mi consectetuer mi a ultricies massa est sed nisl Class aptent taciti</div>
    <svg width="30" height="30" viewBox="0 0 30 30" fill="none" stroke="#fff" stroke-width="2.5" style="margin-top:14px"><path d="M15 3V27M5 17L15 27L25 17"/></svg>
  </div>
</div>

<div class="svc" style="left:832px;top:1458px;width:220px;height:220px">
  <div class="svc-diamond" style="left:0;top:0;width:220px;height:220px;background:var(--steel)"></div>
  <div class="svc-body" style="top:30px">
    <svg width="62" height="60" viewBox="0 0 62 60" fill="none" stroke="#fff" stroke-width="1.8"><circle cx="31" cy="30" r="26"/><path d="M31 4V56M31 30L53 16"/><text x="11" y="27" fill="#fff" stroke="none" font-size="11" font-family="Arial">TAX</text><text x="22" y="47" fill="#fff" stroke="none" font-size="14" font-family="Arial">$</text><text x="38" y="38" fill="#fff" stroke="none" font-size="13" font-family="Arial">%</text></svg>
    <div class="svc-name">TAX REPRESENTATION</div>
    <div class="svc-desc">Suspendisse quam leo molestie sed luctus quis feugiat in</div>
    <svg width="30" height="30" viewBox="0 0 30 30" fill="none" stroke="#fff" stroke-width="2.5" style="margin-top:16px"><path d="M15 3V27M5 17L15 27L25 17"/></svg>
  </div>
</div>

<section class="abs team"></section>
<h2 class="abs section-title" style="top:1860px;color:var(--white);font-size:27px">OUR TEAM</h2>
<p class="abs team-sub">Sed ut perspiciatis unde omnis iste natus error sit voluptatem accusantium doloremque laudantium</p>

<div class="member" style="left:164px"><div class="member-photo" role="img" aria-label="Portrait photo of a team member"></div><div class="member-name">LENA HART</div><div class="member-desc">Sed ut perspiciatis unde iste<br>natus error sit</div><div class="member-btn">VIEW BIO</div></div>
<div class="member" style="left:390px"><div class="member-photo" role="img" aria-label="Portrait photo of a team member"></div><div class="member-name">MARC AUBRY</div><div class="member-desc">Sed ut perspiciatis unde iste<br>natus error sit</div><div class="member-btn">VIEW BIO</div></div>
<div class="member" style="left:614px"><div class="member-photo" role="img" aria-label="Portrait photo of a team member"></div><div class="member-name">RAVI NOLLER</div><div class="member-desc">Sed ut perspiciatis unde iste<br>natus error sit</div><div class="member-btn">VIEW BIO</div></div>
<div class="member" style="left:839px"><div class="member-photo" role="img" aria-label="Portrait photo of a team member"></div><div class="member-name">SOFIA BRANDT</div><div class="member-desc">Sed ut perspiciatis unde iste<br>natus error sit</div><div class="member-btn">VIEW BIO</div></div>

<h2 class="abs section-title" style="top:2376px;color:var(--ink);font-size:27px">PROJECTS</h2>
<p class="abs projects-sub">Lorem Ipsum is simply dummy text of the printing and typesetting industry. Lorem Ipsum has been the industry's standard dummy text ever since the 1500s, when an unknown printer took a galley of type and scrambled it to make a type</p>

<article class="card" style="left:150px"><div class="card-photo" role="img" aria-label="Business team celebrating in an office" style="background:linear-gradient(135deg,#c9ccd0,#6d7078 60%,#3c3f46)"></div><div class="card-body"><div class="card-tag">Capital, Economy</div><div class="card-title">We Help Your Time Work For Your Money.</div><div class="card-text">Lorem Ipsum is simply dummy text of the printing and typesetting industry. Lorem Ipsum has been the industry's standard dummy text ever since the 1500s, when an unknown printer took a galley of type and scrambled it to make a type</div></div></article>
<article class="card" style="left:451px"><div class="card-photo" role="img" aria-label="Colleagues working together at a meeting table" style="background:linear-gradient(135deg,#8a7460,#3d4a5c 60%,#263444)"></div><div class="card-body"><div class="card-tag">Capital, Economy</div><div class="card-title">You Have Roots Here Now, Grow With Us.</div><div class="card-text">Lorem Ipsum is simply dummy text of the printing and typesetting industry. Lorem Ipsum has been the industry's standard dummy text ever since the 1500s, when an unknown printer took a galley of type and scrambled it to make a type</div></div></article>
<article class="card" style="left:749px"><div class="card-photo" role="img" aria-label="Business people in discussion around laptops" style="background:linear-gradient(135deg,#d9dcdf,#8c9096 55%,#4b4f56)"></div><div class="card-body"><div class="card-tag">Capital, Economy</div><div class="card-title">Experience And Resources By Your Side.</div><div class="card-text">Lorem Ipsum is simply dummy text of the printing and typesetting industry. Lorem Ipsum has been the industry's standard dummy text ever since the 1500s, when an unknown printer took a galley of type and scrambled it to make a type</div></div></article>

<div class="abs dots"><div class="dot"></div><div class="dot on"></div><div class="dot"></div></div>

<section class="abs contact" role="img" aria-label="Harbour with cranes and container ships at dusk, tinted navy"></section>
<h2 class="abs head contact-title">CONTACT US</h2>

<div class="info" style="top:3165px">
  <svg width="44" height="46" viewBox="0 0 44 46" fill="none" stroke="#fff" stroke-width="1.8"><path d="M22 36C14 26 10 20 10 14a12 12 0 0124 0c0 6-4 12-12 22z"/><circle cx="22" cy="14" r="5"/><path d="M12 32C5 34 3 36 3 38c0 3 9 6 19 6s19-3 19-6c0-2-2-4-9-6"/></svg>
  <div><div class="info-label">ADDRESS</div><div class="info-value">14 Rue du Lac, 2000 Neuchâtel CH</div></div>
</div>
<div class="info" style="top:3258px">
  <svg width="44" height="44" viewBox="0 0 44 44" fill="none" stroke="#fff" stroke-width="1.8"><path d="M8 4l7 1 3 9-5 3c2 5 6 9 11 11l3-5 9 3 1 7c-2 4-6 6-10 5C16 35 9 28 6 16 5 11 5 7 8 4z"/></svg>
  <div><div class="info-label">PHONE NUMBER</div><div class="info-value">655.410.2876</div></div>
</div>
<div class="info" style="top:3348px">
  <svg width="44" height="40" viewBox="0 0 44 40" fill="none" stroke="#fff" stroke-width="1.8"><rect x="3" y="7" width="38" height="26"/><path d="M3 7l19 15L41 7M3 33l14-13M41 33L27 20"/></svg>
  <div><div class="info-label">EMAIL US</div><div class="info-value">info@velmaro-consult.com</div></div>
</div>

<div class="field" style="top:3097px;height:42px">Name</div>
<div class="field" style="top:3147px;height:42px">Email</div>
<div class="field" style="top:3196px;height:42px">Phone</div>
<div class="field" style="top:3248px;height:90px;left:624px">Message</div>
<div class="abs btn-light">SUBMIT NOW</div>

<svg class="abs" style="left:0;top:3460px" width="1200" height="242" viewBox="0 0 1200 242"><path d="M0 120L600 22L1200 120V242H0Z" fill="#fff"/></svg>
<div class="abs" style="left:568px;top:3450px;width:50px;height:50px;border-radius:10px;background:var(--navy);border:2px solid #fff"></div>

<div class="abs foot-links" style="left:0;width:1200px">
  <span style="left:309px">HOME</span>
  <span style="left:401px">ABOUT US</span>
  <span style="left:526px">OUR SERVICES</span>
  <span style="left:681px">TEAM</span>
  <span style="left:770px">CONTACT</span>
</div>
<p class="abs copy">© 2020 Company Name&nbsp; All right reserved</p>
<div class="abs social" style="left:509px"></div>
<div class="abs social" style="left:554px"></div>
<div class="abs social" style="left:599px"></div>

</body>
</html>
```